Software Product Flyer Design

A established czech software company needs a marketing flyer to promote their software product and its modules.
The overall feel of the flyer must to be serious, but also eye-catching, enticing, clever and bold to attract customers.
Unifying graphic element is the new product logo.
The flyer would be A4, colour both sides and folded once (to give 4 pages of A5).
Title page - product logo with module name and module icon, short presentation of the product and list of its key features.
Inside pages - detailed informations with screenshots or graphical schemas.
Back side - informations about technical requirements and user support, contacts (address, phone, fax, e-mail, web pages - no social networks).
Product logo, module icon and some images attached.
Updates
Hello,
Reason: For organizational reasons we extending the deadline by 10 days.
FYI: We have uploaded the new ZIP file with previous version of our flyer.
Attached PDF file with text for inner pages.
Target Market(s)
Existing or new customers like municipalities, public authorities and nonprofit organizations.
Industry/Entity Type
Marketing
Requirements
Must have
- Winning designer must provide a template for Adobe InDesign based on his graphic design.
Avoid to using exotic fonts - in Czech we use Latin Extended characters (like áéěíýůčřžšťďň).
Nice to have
- Using graphic motif from product logo like as attached splash screen.

```html
<!DOCTYPE html>
<html lang="cs">
<head>
<meta charset="utf-8">
<title>Velto – Majetek – leták</title>
<link href="https://fonts.googleapis.com/css2?family=Open+Sans:wght@400;600;700&family=Arimo:wght@700&display=swap" rel="stylesheet">
<style>
:root{
  --dark:#3b3e43;
  --dark-2:#2f3236;
  --orange:#ee5a1c;
  --white:#ffffff;
  --paper:#f4f4f4;
  --text:#333538;
  --muted:#6a6d72;
  --stage:#e6e6e6;
}
*{box-sizing:border-box;margin:0;padding:0}
html,body{width:1200px;height:809px;overflow:hidden;background:var(--stage);font-family:"Open Sans",Arial,sans-serif;color:var(--text)}
.spread{position:absolute;left:28px;top:0;width:1144px;height:809px;display:flex;box-shadow:0 4px 18px rgba(0,0,0,.25)}
.page{position:relative;width:572px;height:809px;overflow:hidden;background:var(--white)}

/* back page */
.tech{position:absolute;left:0;top:0;width:572px;height:372px;background:var(--dark);color:var(--white)}
.tech-title{position:absolute;left:22px;top:12px;font-size:21px;font-weight:400}
.tech-intro{position:absolute;left:22px;top:44px;width:520px;font-size:9.5px;line-height:1.35;color:#d9dadc}
.tech-rule{position:absolute;left:22px;right:22px;top:76px;height:1px;background:#7d8085}
.shot{background:linear-gradient(180deg,#fafafa,#dfe3e6);border:3px solid #e9e9e9}
.tech .shot{position:absolute;left:22px;top:88px;width:132px;height:94px}
.server-tab{position:absolute;left:156px;top:88px;width:26px;height:94px;background:var(--orange);display:flex;align-items:center;justify-content:center}
.server-tab span{transform:rotate(-90deg);font-weight:700;font-size:13px;letter-spacing:1px;white-space:nowrap}
.server-list{position:absolute;left:196px;top:90px;width:350px;list-style:none;font-size:9.5px;line-height:1.35;color:#e4e5e7}
.server-list li{position:relative;padding-left:16px;margin-bottom:8px}
.server-list li::before,.station-list li::before{content:"";position:absolute;left:2px;top:4px;width:6px;height:6px;border-radius:50%;background:var(--white)}
.station-band{position:absolute;left:0;top:198px;width:572px;height:27px;background:var(--orange);padding-left:22px;font-size:15px;font-weight:700;line-height:27px}
.station-list{position:absolute;left:22px;top:236px;width:530px;list-style:none;font-size:10px;line-height:1.35;color:#e4e5e7}
.station-list li{position:relative;padding-left:16px;margin-bottom:2px}

.support{position:absolute;left:0;top:388px;width:572px;text-align:center}
.support-title{font-size:21px;font-weight:700;color:var(--orange)}
.support-intro{margin:6px auto 0;width:420px;font-size:11px;line-height:1.35;color:var(--text)}
.support-list{list-style:none;margin:14px auto 0;width:260px;font-size:9.5px;line-height:1.3;color:var(--muted)}
.support-list li{border-bottom:1px solid #b9bbbe;padding:2px 0}
.contact{position:absolute;left:0;top:640px;width:572px;text-align:center;font-size:9.5px;line-height:1.35;color:var(--text)}
.brand{display:inline-flex;align-items:center;gap:6px;font-family:"Open Sans",Arial,sans-serif;font-weight:700;color:var(--dark);letter-spacing:.5px}
.brand .dot{border-radius:50%;background:var(--orange)}
.contact .brand{font-size:34px;margin-bottom:4px}
.contact .brand .dot{width:20px;height:20px}
.back-foot{position:absolute;left:0;bottom:0;width:572px;height:16px;background:var(--orange)}

/* front page */
.side-strip{position:absolute;left:0;top:0;width:132px;height:809px;background:var(--dark)}
.side-strip .shot{position:absolute;left:14px;width:106px;height:76px}
.front-foot{position:absolute;left:0;bottom:0;width:132px;height:16px;background:var(--dark-2)}
.cover .brand{position:absolute;left:178px;top:84px;font-size:42px}
.cover .brand .dot{width:24px;height:24px}
.module{position:absolute;left:270px;top:150px;width:270px}
.module-icon{position:absolute;right:0;top:0;width:26px;height:30px;background:linear-gradient(180deg,#f2f2f2,#9a9ca0);border:1px solid #555}
.module-name{margin-top:26px;font-family:"Arimo",Arial,sans-serif;font-size:34px;font-weight:700;color:var(--dark);letter-spacing:1px}
.module-rule{height:1px;background:var(--orange);margin-top:4px}
.module-lead{margin-top:8px;font-size:12px;line-height:1.35;color:var(--orange);text-align:justify}
.benefits{position:absolute;left:190px;top:640px;width:350px}
.benefits-head{display:flex;align-items:center;gap:8px;font-family:"Arimo",Arial,sans-serif;font-size:18px;font-weight:700;color:var(--dark)}
.benefits-icon{width:24px;height:28px;background:linear-gradient(135deg,#f0a030,#c46a10)}
.benefits-rule{height:1px;background:var(--orange);margin:4px 0 6px}
.benefits ul{list-style:none;font-family:"Arimo",Arial,sans-serif;font-size:13px;font-weight:700;color:var(--text);line-height:1.3}
.benefits li{display:flex;align-items:center;gap:8px}
.benefits li svg{flex:none}
.benefits-end{height:1px;background:var(--orange);margin-top:10px}
</style>
</head>
<body>
<main class="spread">

  <section class="page back">
    <div class="tech">
      <h2 class="tech-title">Technické podmínky</h2>
      <p class="tech-intro">Systém VELTO umožňuje nasazení prakticky u jakéhokoli zákazníka v jakémkoli prostředí bez ohledu na počet uživatelů nebo množství dat.</p>
      <div class="tech-rule"></div>
      <div class="shot" role="img" aria-label="Snímek obrazovky serverové správy"></div>
      <div class="server-tab"><span>SERVER</span></div>
      <ul class="server-list">
        <li>Operační systém Fenestra XP a novější nebo operační systém Tuxon</li>
        <li>Systém vyžaduje nainstalovaný runtime pro Kava 1.7, databázi PostBase ve verzi 9.2, webový server Apex Catkin 7.0 a JMS systém ActiveQueue</li>
        <li>Doporučená velikost RAM je minimálně 4 GB</li>
        <li>Minimální disková velikost je 20 GB</li>
      </ul>
      <div class="station-band">Pracovní stanice</div>
      <ul class="station-list">
        <li>Operační systém Fenestra XP a novější</li>
        <li>Minimální velikost RAM je 2 GB</li>
        <li>Minimální diskový prostor je 5 GB</li>
        <li>Pro běh programu VELTO na pracovní stanici je zapotřebí runtime pro Kava 1.7 (je součástí instalace)</li>
        <li>Pro zobrazení a tisk sestav je zapotřebí prohlížeč PDF souborů (Adeo Reader X nebo jiný)</li>
        <li>Podporované kancelářské balíky: Microdesk Office 2007 a novější, FreeDesk 3.0 a novější a OpenDesk 3.0 a novější</li>
      </ul>
    </div>

    <div class="support">
      <h2 class="support-title">Uživatelská podpora</h2>
      <p class="support-intro">Společnost Norvik si zakládá na důvěrném vztahu se zákazníky, který se podařilo za více než 20 let existence firmy vybudovat.</p>
      <ul class="support-list">
        <li>Regionální zastoupení po celé České republice</li>
        <li>Individuální přístup ke každému zákazníkovi</li>
        <li>Pracovní postupy zpracované formou názorných prezentací</li>
        <li>Tichá aktualizace programů přes internet</li>
        <li>Školení, metodická podpora a telefonické poradenství</li>
        <li>Aktuální informace na webových stránkách</li>
      </ul>
    </div>

    <address class="contact" style="font-style:normal">
      <div class="brand"><span class="dot"></span>velto</div>
      <div>VELTO LTD</div>
      <div>170 Mine St., Country, Address Line 2</div>
      <div>Email : info@velto-soft.example , Website : www.velto-soft.example</div>
      <div>Phone : 1234567890 ; Fax : 1234567890</div>
    </address>
    <div class="back-foot"></div>
  </section>

  <section class="page cover">
    <div class="side-strip">
      <div class="shot" style="top:330px" role="img" aria-label="Snímek obrazovky – seznam majetku"></div>
      <div class="shot" style="top:420px" role="img" aria-label="Snímek obrazovky – karta majetku"></div>
      <div class="shot" style="top:510px" role="img" aria-label="Snímek obrazovky – úvodní okno"></div>
      <div class="shot" style="top:600px" role="img" aria-label="Snímek obrazovky – přehled odpisů"></div>
      <div class="front-foot"></div>
    </div>

    <div class="brand"><span class="dot"></span>velto</div>

    <div class="module">
      <div class="module-icon" role="img" aria-label="Ikona modulu Majetek"></div>
      <h1 class="module-name">MAJETEK</h1>
      <div class="module-rule"></div>
      <p class="module-lead">Lorem ipsum dolor sit amet, consectetur adipisicing elit, sed do eiusmod tempor incididunt ut labore et dolore magna aliqua. Ut enim ad minim veniam, quis nostrud exercitation ullamco laboris nisi ut aliquip ex ea commodo consequat.</p>
    </div>

    <div class="benefits">
      <h2 class="benefits-head">Co vam prinese <span class="benefits-icon" role="img" aria-label="Ikona přínosů"></span></h2>
      <div class="benefits-rule"></div>
      <ul>
        <li><svg width="9" height="10" viewBox="0 0 9 10"><path d="M0 0L9 5L0 10Z" fill="#333538"/></svg>Here will go key feature</li>
        <li><svg width="9" height="10" viewBox="0 0 9 10"><path d="M0 0L9 5L0 10Z" fill="#333538"/></svg>Here will go key feature</li>
        <li><svg width="9" height="10" viewBox="0 0 9 10"><path d="M0 0L9 5L0 10Z" fill="#333538"/></svg>Here will go key feature</li>
        <li><svg width="9" height="10" viewBox="0 0 9 10"><path d="M0 0L9 5L0 10Z" fill="#333538"/></svg>Here will go key feature</li>
      </ul>
      <div class="benefits-end"></div>
    </div>
  </section>

</main>
</body>
</html>
```